Real Estate Company / Capital Needs Cards!

need business cards designed using the logos that were just designed by pixelbarn.

Reason: per designers request deadline extended 1 day…thank you.

Target Market(s)

Investors and clients looking to purchase real estate or invest in the business.

Industry/Entity Type

Business

Requirements
Must have
• two designs - one for the real estate logo and one for the capital logo, similar but slightly different.
Nice to have
• something to make it pop (perhaps on the back)
Should not have
• much color

```html
<!DOCTYPE html>
<html lang="en">
<head>
<meta charset="utf-8">
<title>Corvane Real Estate – Business Cards</title>
<link href="https://fonts.googleapis.com/css2?family=Open+Sans:wght@400;600&display=swap" rel="stylesheet">
<style>
  :root {
    --stage: #e9e6e2;
    --card: #ffffff;
    --ink: #3a3a3a;
    --ink-soft: #555555;
    --mark: #8a8a8a;
    --rule: #7a7a7a;
    --ghost: #ececec;
  }
  * { box-sizing: border-box; margin: 0; padding: 0; }
  html, body { width: 1200px; height: 498px; overflow: hidden; }
  body {
    background: var(--stage);
    font-family: "Open Sans", Arial, sans-serif;
    color: var(--ink);
    position: relative;
  }
  .card {
    position: absolute;
    top: 94px;
    width: 540px;
    height: 310px;
    background: var(--card);
    border-radius: 30px;
    box-shadow: 0 4px 14px rgba(0,0,0,0.12);
    overflow: hidden;
  }
  .card--front { left: 40px; }
  .card--back { left: 620px; }

  .brand { display: flex; align-items: center; gap: 12px; position: absolute; }
  .brand__square { background: var(--mark); flex: none; }
  .brand__name {
    font-weight: 400;
    color: var(--mark);
    letter-spacing: 0.08em;
    line-height: 1.15;
    text-transform: uppercase;
    white-space: nowrap;
  }

  .card--front .brand { left: 34px; top: 46px; }
  .card--front .brand__square { width: 50px; height: 50px; }
  .card--front .brand__name { font-size: 19px; }

  .holder {
    position: absolute;
    right: 28px;
    top: 60px;
    width: 236px;
    text-align: right;
    font-size: 17px;
    padding-bottom: 6px;
    border-bottom: 3px solid var(--rule);
  }
  .holder__name { font-weight: 600; }

  .ghost-square {
    position: absolute;
    right: 40px;
    top: 116px;
    width: 160px;
    height: 160px;
    border-radius: 14px;
    background: var(--ghost);
  }

  .contacts {
    position: absolute;
    left: 40px;
    bottom: 30px;
    list-style: none;
    font-size: 16px;
    color: var(--ink-soft);
    line-height: 1.5;
  }
  .contacts li { display: flex; align-items: center; gap: 5px; }
  .contacts svg { width: 12px; height: 12px; fill: var(--ink-soft); flex: none; }
  .contacts .contacts__small { font-size: 14px; }

  .card--back .brand { left: 50%; top: 88px; transform: translateX(-50%); gap: 18px; }
  .card--back .brand__square { width: 92px; height: 92px; }
  .card--back .brand__name { font-size: 36px; }
  .card--back .brand__name span { display: block; font-size: 24px; letter-spacing: 0.16em; }

  .website {
    position: absolute;
    left: 0; right: 0;
    top: 222px;
    text-align: center;
    font-size: 15px;
    letter-spacing: 0.2em;
    color: var(--ink);
  }
  .website strong { font-weight: 600; }
</style>
</head>
<body>
  <section class="card card--front">
    <div class="brand">
      <div class="brand__square"></div>
      <div class="brand__name">Corvane<br>Real Estate</div>
    </div>
    <p class="holder"><span class="holder__name">Your Name,</span> Title</p>
    <div class="ghost-square"></div>
    <ul class="contacts">
      <li><svg viewBox="0 0 24 24"><path d="M6.6 10.8a15 15 0 0 0 6.6 6.6l2.2-2.2c.3-.3.7-.4 1-.2 1.1.4 2.3.6 3.6.6.6 0 1 .4 1 1V20c0 .6-.4 1-1 1A17 17 0 0 1 3 4c0-.6.4-1 1-1h3.5c.6 0 1 .4 1 1 0 1.3.2 2.5.6 3.6.1.3 0 .7-.2 1z"/></svg>555-014-2270</li>
      <li><svg viewBox="0 0 24 24"><path d="M6 2h12v6H6zM4 9h16a2 2 0 0 1 2 2v7h-4v4H6v-4H2v-7a2 2 0 0 1 2-2zm4 7v4h8v-4z"/></svg>555-019-4836</li>
      <li class="contacts__small"><svg viewBox="0 0 24 24"><path d="M2 5h20v14H2zm2 2v.5l8 5 8-5V7z"/></svg>hello@corvanerealestate.com</li>
      <li class="contacts__small">Street Name, City Name State ZipCode</li>
    </ul>
  </section>

  <section class="card card--back">
    <div class="brand">
      <div class="brand__square"></div>
      <div class="brand__name">Corvane<span>Real Estate</span></div>
    </div>
    <p class="website">www.<strong>corvanerealestate</strong>.com</p>
  </section>
</body>
</html>
```